Facebook Page Design for a Medical Billing Business

We need help designing a facebook page that is professional, yet friendly that will attract medical practitioners (doctors, therapists, nutritionists, chiropractors, etc) to check out and follow our business. I have attached our logo which must be incorporated in the design.

```html
<!DOCTYPE html>
<html lang="en">
<head>
<meta charset="UTF-8">
<title>Vega Claims Partners – Page Cover</title>
<link rel="stylesheet" href="https://fonts.googleapis.com/css2?family=Oswald:wght@600&family=Tinos:wght@400;700&display=swap">
<style>
  :root {
    --stage: #eceef2;
    --magenta: #b516c9;
    --violet: #5a1fd6;
    --royal: #2a4fe6;
    --sky: #1f8ff0;
    --cyan: #19f0f2;
    --white: #ffffff;
    --ink: #000000;
    --mark-violet: #8a4cf0;
  }
  * { box-sizing: border-box; margin: 0; padding: 0; }
  html, body { width: 1200px; height: 800px; overflow: hidden; background: var(--stage); }
  .stage {
    width: 1200px; height: 800px;
    display: flex; align-items: center; justify-content: center; gap: 30px;
  }
  .profile-badge {
    flex: none;
    width: 250px; height: 250px; border-radius: 50%;
    background: var(--ink);
    display: flex; align-items: center; justify-content: center;
    position: relative;
  }
  .profile-badge::before {
    content: ""; position: absolute; inset: 10px; border-radius: 50%;
    border: 2px solid transparent;
    background: linear-gradient(135deg, var(--magenta), var(--sky)) border-box;
    -webkit-mask: linear-gradient(#000 0 0) padding-box, linear-gradient(#000 0 0);
    -webkit-mask-composite: xor; mask-composite: exclude;
  }
  .profile-name {
    max-width: 170px;
    font-family: "Tinos", serif; font-weight: 400;
    color: var(--mark-violet); text-align: center;
    font-size: 20px; line-height: 1.2; letter-spacing: 2px;
  }
  .cover {
    flex: none;
    width: 860px; height: 328px; position: relative; overflow: hidden;
    background:
      radial-gradient(circle at 28% 45%, rgba(255,255,255,0.12), transparent 35%),
      linear-gradient(100deg, var(--magenta) 0%, var(--violet) 40%, var(--royal) 70%, var(--sky) 100%);
    color: var(--white);
  }
  .cover-glow {
    position: absolute; left: 40px; bottom: -150px; width: 320px; height: 220px;
    border-radius: 50%; background: rgba(220,60,230,0.45);
  }
  .cover-dots {
    position: absolute; left: 0; top: 0; width: 95px; height: 140px;
    background: linear-gradient(135deg, rgba(255,255,255,0.35), transparent 70%);
  }
  .brand-name {
    position: absolute; left: 0; width: 560px; top: 100px; text-align: center;
    font-family: "Tinos", serif; font-weight: 400; font-size: 24px; letter-spacing: 2px;
    line-height: 1;
  }
  .headline {
    position: absolute; left: 0; width: 560px; top: 178px; text-align: center;
    font-family: "Oswald", sans-serif; font-weight: 600; font-size: 34px;
    color: var(--cyan); letter-spacing: 0.2px; line-height: 1;
  }
  .tagline {
    position: absolute; left: 100px; width: 360px; top: 226px;
    display: flex; align-items: center; gap: 6px;
    font-family: "Tinos", serif; font-size: 11px; white-space: nowrap;
  }
  .tagline::before, .tagline::after { content: ""; flex: 1; height: 1px; background: var(--white); }
  .contact-button {
    position: absolute; left: 233px; top: 257px; width: 94px; height: 21px;
    border: 1.5px solid var(--white); border-radius: 6px;
    font-family: "Tinos", serif; font-weight: 700; font-size: 13px; color: var(--cyan);
    display: flex; align-items: center; justify-content: center;
  }
  .contact-row {
    position: absolute; left: 0; width: 560px; top: 287px;
    display: flex; gap: 8px; align-items: center; justify-content: center;
    font-family: "Tinos", serif; font-size: 11px; white-space: nowrap;
  }
  .contact-item { display: flex; align-items: center; gap: 3px; }
  .contact-item svg { width: 11px; height: 11px; }
  .medical-art {
    position: absolute; left: 500px; top: 27px; width: 300px; height: 278px;
    border-radius: 40% 45% 40% 45%;
    background: radial-gradient(circle at 60% 45%, #3fc4f5 0%, rgba(40,150,240,0.55) 45%, rgba(40,120,240,0) 72%);
  }
</style>
</head>
<body>
<main class="stage">
  <div class="profile-badge">
    <p class="profile-name">VEGA<br>CLAIMS<br>PARTNERS</p>
  </div>

  <section class="cover">
    <div class="cover-glow"></div>
    <div class="cover-dots"></div>

    <p class="brand-name">VEGA CLAIMS PARTNERS</p>

    <h1 class="headline">VEGA CLAIMS PARTNERS, LLC</h1>
    <p class="tagline">Medical Billing Tailored To Your Practices Needs</p>
    <div class="contact-button">Contact Now</div>

    <div class="contact-row">
      <span class="contact-item">
        <svg viewBox="0 0 12 12"><rect x="0.5" y="0.5" width="11" height="11" rx="2" fill="none" stroke="#19f0f2"/><path d="M4 3l1 2-1 1c.5 1 1 1.5 2 2l1-1 2 1-1 1.5C5 9 3 7 2.8 4.2z" fill="#19f0f2"/></svg>
        555-010-0123
      </span>
      <span class="contact-item">
        <svg viewBox="0 0 12 12"><rect x="0.5" y="0.5" width="11" height="11" rx="2" fill="none" stroke="#19f0f2"/><path d="M4 3l5 3-2 .5 1.5 2.5-1 .5-1.5-2.5L4.5 8.5z" fill="#19f0f2"/></svg>
        www.vegaclaimspartners.com
      </span>
      <span class="contact-item">
        <svg viewBox="0 0 12 12"><rect x="0.5" y="0.5" width="11" height="11" rx="2" fill="none" stroke="#19f0f2"/><rect x="2.5" y="3.5" width="7" height="5" fill="none" stroke="#19f0f2"/><path d="M2.5 3.5L6 6.5l3.5-3" fill="none" stroke="#19f0f2"/></svg>
        Admin@vegaclaimspartners.com
      </span>
    </div>

    <div class="medical-art" role="img" aria-label="Illustration of a stethoscope, a blue shield with a white medical cross and scattered pills"></div>
  </section>
</main>
</body>
</html>
```